Business card design for my company.
I would like the card's background colour to be black. You can also see our web site to get an idea of our brand. https://www.tmwhomecrafting.com.au/
- Name
- Email

```html
<!DOCTYPE html>
<html lang="en">
<head>
<meta charset="utf-8">
<title>TMW Home Crafting – Business Card</title>
<link rel="stylesheet" href="https://fonts.googleapis.com/css2?family=Montserrat:wght@400;500;700;800&display=swap">
<style>
  :root {
    --stage: #2a2a2c;
    --card-black: #141414;
    --brand-green: #0b9a4a;
    --green-soft: #1aa556;
    --green-deep: #07803c;
    --text-light: #f2f2f2;
    --text-muted: #d8d8d8;
  }
  * { box-sizing: border-box; margin: 0; padding: 0; }
  html, body {
    width: 1200px; height: 900px; overflow: hidden;
    background: var(--stage);
    font-family: "Montserrat", sans-serif;
  }
  .stage {
    width: 1200px; height: 900px;
    display: flex; flex-direction: column; align-items: center; justify-content: center;
    gap: 60px;
  }
  .card {
    width: 616px; height: 352px;
    border-radius: 30px;
    position: relative;
    overflow: hidden;
    box-shadow: 0 14px 30px rgba(0,0,0,.35);
  }

  /* Front */
  .card-front { background: var(--card-black); color: var(--text-light); }
  .front-brand {
    position: absolute; top: 62px; left: 292px;
    display: flex; align-items: center; gap: 12px;
  }
  .brand-square { width: 18px; height: 18px; background: var(--brand-green); }
  .brand-name {
    font-weight: 800; font-size: 30px; letter-spacing: 1px;
    color: var(--text-light); text-transform: uppercase; line-height: 1;
  }
  .front-details {
    position: absolute; top: 170px; left: 40px;
    display: flex; align-items: stretch;
  }
  .person { text-align: right; padding-right: 16px; }
  .person-name { font-weight: 700; font-size: 30px; color: var(--brand-green); line-height: 1.1; }
  .person-role { font-size: 15px; color: var(--text-muted); margin-top: 6px; }
  .divider { width: 2px; background: var(--brand-green); margin-right: 16px; }
  .contacts { list-style: none; display: flex; flex-direction: column; gap: 6px; justify-content: center; }
  .contact { display: flex; align-items: center; gap: 8px; font-size: 15px; color: var(--text-light); }
  .contact svg { width: 14px; height: 14px; flex: none; }
  .address {
    position: absolute; top: 280px; left: 90px;
    font-size: 15px; color: var(--text-light);
  }

  /* Back */
  .card-back {
    background: linear-gradient(135deg, var(--green-soft), var(--brand-green) 60%, var(--green-deep));
    display: flex; align-items: center; justify-content: center;
  }
  .back-brand {
    font-weight: 800; font-size: 46px; letter-spacing: 3px;
    text-transform: uppercase; color: #0a7a3a; text-align: center; line-height: 1.15;
  }
</style>
</head>
<body>
<main class="stage">
  <section class="card card-front" aria-label="Business card front">
    <div class="front-brand">
      <span class="brand-square"></span>
      <span class="brand-name">TMW Home Crafting</span>
    </div>
    <div class="front-details">
      <div class="person">
        <p class="person-name">Liam Hartley</p>
        <p class="person-role">General Manager</p>
      </div>
      <div class="divider"></div>
      <ul class="contacts">
        <li class="contact">
          <svg viewBox="0 0 16 16" fill="#f2f2f2"><path d="M3 1h3l1.5 3.5-2 1.3a9 9 0 0 0 4.7 4.7l1.3-2L15 10v3a2 2 0 0 1-2 2A12 12 0 0 1 1 3a2 2 0 0 1 2-2z"/></svg>
          0400 123 456
        </li>
        <li class="contact">
          <svg viewBox="0 0 16 16" fill="none" stroke="#f2f2f2" stroke-width="1.6"><rect x="1" y="3" width="14" height="10"/><path d="M1 3l7 6 7-6"/></svg>
          info@tmwhomecrafting.com.au
        </li>
        <li class="contact">
          <svg viewBox="0 0 16 16" fill="none" stroke="#f2f2f2" stroke-width="1.4"><circle cx="8" cy="8" r="6.5"/><path d="M1.5 8h13M8 1.5c2.5 2.5 2.5 10.5 0 13M8 1.5c-2.5 2.5-2.5 10.5 0 13"/></svg>
          www.tmwhomecrafting.com.au
        </li>
      </ul>
    </div>
    <p class="address">Eastbank, Tasmania, Australia</p>
  </section>

  <section class="card card-back" aria-label="Business card back">
    <p class="back-brand">TMW<br>Home Crafting</p>
  </section>
</main>
</body>
</html>
```